Business card for Luxury Portable Restroom Trailer company

We are a Luxury Portable Restroom Trailer Company Called FALCRIDGE HIRES. Based in Orange County California. We provide portable restroom trailers for events, such as, Weddings, Concerts, Charity events, Sporting events, Tournaments, Corporate events, ect. We rent and Sell the Luxury restrooms. Our colors are white, grey, and Orange. As you will see in the logo we uploaded.
There are 2 people in the company so the names and titles will change for the 3 people but card will remain the same. Here is the information for each Person: Dwight Penner CFO 555 318-0476
next Person: Leon Marchetti VP 555 318-0476
Next Person: Owen Marchetti CEO 555 318-0476
Information to include on the card: Luxury Restroom Trailers Rental and Sales. Weddings, Concerts, Charity, Sporting and Corp. Events.

```html
<!DOCTYPE html>
<html lang="en">
<head>
<meta charset="utf-8">
<title>Falcridge Hires – Business Card</title>
<link rel="stylesheet" href="https://fonts.googleapis.com/css2?family=Montserrat:wght@400;700;800&display=swap">
<style>
  :root {
    --orange: #e8621f;
    --orange-deep: #d9541a;
    --charcoal: #4a4a4d;
    --ink: #3c3c3e;
    --card: #f7f5f2;
    --backdrop: #e4e1dc;
    --light-text: #e9e6e2;
  }
  * { margin: 0; padding: 0; box-sizing: border-box; }
  html, body {
    width: 1200px; height: 897px; overflow: hidden;
    background: var(--backdrop);
    font-family: "Montserrat", sans-serif;
  }
  .business-card {
    position: absolute; left: 80px; top: 163px;
    width: 1040px; height: 570px;
    background: var(--card);
    border-radius: 26px;
    overflow: hidden;
    box-shadow: 0 10px 30px rgba(0,0,0,0.12);
  }
  .brand-name {
    position: absolute; left: 48px; top: 70px;
    font-weight: 800; font-size: 50px; letter-spacing: 1px;
    color: var(--orange);
    line-height: 1;
  }
  .contact-band {
    position: absolute; left: 0; top: 208px;
    width: 807px; height: 253px;
    background: var(--charcoal);
  }
  .accent-band {
    position: absolute; left: 807px; top: 208px;
    width: 233px; height: 253px;
    background: var(--orange-deep);
  }
  .accent-ring {
    position: absolute; left: 679px; top: 206px;
    width: 257px; height: 257px;
    border-radius: 50%;
    background: var(--card);
    border: 18px solid var(--orange);
    box-shadow: 0 0 0 5px var(--card);
  }
  .person-name {
    position: absolute; left: 48px; top: 234px;
    font-weight: 700; font-size: 35px; letter-spacing: 1px;
    color: var(--orange);
  }
  .person-title {
    position: absolute; left: 48px; top: 279px;
    font-weight: 400; font-size: 24px; letter-spacing: 1px;
    color: var(--light-text);
  }
  .title-rule {
    position: absolute; left: 48px; top: 313px;
    width: 20px; height: 2px; background: var(--orange);
  }
  .contact-list { list-style: none; }
  .contact-item {
    position: absolute; left: 48px;
    display: flex; align-items: center; gap: 10px;
    font-size: 23px; font-weight: 400; letter-spacing: 0.6px;
    color: var(--light-text);
  }
  .contact-item svg { width: 18px; height: 18px; flex: none; }
  .contact-phone { top: 330px; }
  .contact-email { top: 371px; }
  .contact-web { top: 411px; }
  .service-line {
    position: absolute; left: 48px; top: 476px;
    font-weight: 700; font-size: 21px; letter-spacing: 0.6px;
    color: var(--orange);
  }
  .event-types {
    position: absolute; left: 48px; top: 509px;
    font-weight: 400; font-size: 21px; letter-spacing: 0.6px;
    color: var(--ink);
  }
</style>
</head>
<body>
  <div class="business-card">
    <div class="brand-name">FALCRIDGE HIRES</div>

    <div class="contact-band"></div>
    <div class="accent-band"></div>
    <div class="accent-ring"></div>

    <div class="person-name">OWEN MARCHETTI</div>
    <div class="person-title">CEO</div>
    <div class="title-rule"></div>

    <ul class="contact-list">
      <li class="contact-item contact-phone">
        <svg viewBox="0 0 24 24"><path fill="#e8621f" d="M6.6 10.8a15.1 15.1 0 0 0 6.6 6.6l2.2-2.2c.3-.3.7-.4 1-.2 1.1.4 2.3.6 3.6.6.6 0 1 .4 1 1V20c0 .6-.4 1-1 1A17 17 0 0 1 3 4c0-.6.4-1 1-1h3.5c.6 0 1 .4 1 1 0 1.3.2 2.5.6 3.6.1.3 0 .7-.2 1z"/></svg>
        <span>555 318-0476</span>
      </li>
      <li class="contact-item contact-email">
        <svg viewBox="0 0 24 24"><path fill="#e8621f" d="M2 8l10-6 10 6v13H2z"/><path fill="#4a4a4d" d="M3.5 9.5l8.5 5.5 8.5-5.5" stroke="#4a4a4d" stroke-width="1.4" fill="none"/></svg>
        <span>owen@falcridgehires.com</span>
      </li>
      <li class="contact-item contact-web">
        <svg viewBox="0 0 24 24"><circle cx="12" cy="12" r="10" fill="#e8621f"/><path d="M2 12h20M12 2c3 3 3 17 0 20M12 2c-3 3-3 17 0 20" stroke="#4a4a4d" stroke-width="1.4" fill="none"/></svg>
        <span>www.falcridgehires.com</span>
      </li>
    </ul>

    <div class="service-line">Luxury Restroom Trailers Rental and Sales</div>
    <div class="event-types">Weddings | Concerts | Charity | Sporting | Corp</div>
  </div>
</body>
</html>
```